Calder Aviation website

We are an aviation company based in Miramar, FL but with worldwide coverage. We are involved in commercial aircraft (mostly freighters) trading, sale & leasing. Specifically, we specialized in freighters of the Veltram family (V316, V328, V335, V342, V359). We also assist with financing, sale/leaseback. Handle special aviation projects and provide consultancy services. Currently engaged in a Veltram 359 passenger to Freighter conversion (P2F).

Website Preliminary Initial Content/Sections as follows:

About Us
Founded in 2011, Calder Aviation's management has many years of experience in Aviation, a strong background in scheduled airlines with emphasis in all cargo operations, freight forwarding supply chain and freight logistics, as well as ACMI and CMI operations.

Calder’s focuses in facilitating wet and dry lease operations, charter and ACMI programs consultancy, aircraft sales, leasing and procurement, aviation consultancy and aircraft management.

Calder team is a hands-on reliable alternative that works toward achieving your aircraft and aviation objectives by meeting your requirements and timeframe throughout professional and personalized service.

Tiberio Salcedo has over three decades of experience in the aviation field including aircraft maintenance, airline management, supply chain and logistics management. Tiberio is a true entrepreneur with proven experience and expertise on the multiple facets of the commercial aviation industry throughout the creation and development of a cluster of aviation entities. Tiberio is the founder and former sole member/chairman of 64 Air, a Veltram 342 All-Cargo U.S. Certificated Air Carrier created from scratch in 2014 which nowadays conforms a superb growing airline platform with an immaculate compliance operational record.

Services

Aircraft Finance, Trading, Procurement and Leasing
Calder buys, sells, leases and facilitates aircraft trading while specializes in structured aircraft investment projects. Calder has deep industry relationships and years of expertise, allowing to successfully execute lease transactions. We assist airlines, financial institutions and leasing companies when selling or purchasing aircraft.

Aircraft Available for Sale/Lease

Sale/Leaseback
Sale-leaseback is a method of financing. If your company needs liquidity, your aircraft or engine can serve as collateral for a loan throughout a sale-leaseback transaction. Sale-leaseback can free the equity tied up in aircraft or asset. Even if there is no pressing need for funds, a sale-leaseback allows you to use the equity tied up in your aircraft in a more productive fashion. Leaseback arrangements are usually employed because they confer financing, accounting or taxation benefits.

Passenger to Freighter Conversion (P2F)
Pandemic has seen the resurgence of operators packing freight into the main cabins of passenger aircraft. Carriers have been allowed to transport cargo in the cabin by removing passenger seats completely. NAB/CARO have established exemptions that allow operators to fly in “Preighter” configuration for a limited time. Calder is closely working with a U.S. group that is developing a Class E Supplemental Type Certificate (STC) for applicability on V359 aircraft which will include a cargo door for containerized freight. Final approvals are expected during first quarter of 2022.
Wet lease
Throughout our deep relationships within the industry, Calder facilitates short or long-term wet leases to airlines and qualified parties around the globe, whereby we provide the Aircraft, Crews, Maintenance and Insurance (ACMI) worldwide services at competitive rates. We also specialize in AM leases where the aircraft is registered onto Lessee´s AOC with all maintenance services included in the rates, covering all maintenance risks, or CM or CMI where the client provides the aircraft.

Dry Lease
We offer aircraft from our own portfolio on dry lease or could engage in procuring the aircraft of your choice.

Asset & Aircraft Management
We provide aircraft owners Aircraft Management services, where we manage the technical side of the aircraft or the asset. Calder also provides Harlow Dynamics engines trading, repair and full management services. We also buy Veltram/Skylane surplus inventory.

Worldwide Charters
We facilitate the arrangement of full charters to airlines and logistics companies. Certain territory restrictions may apply.

Aviation Consultancy
We provide airline consultancy services for new or special projects. Calder also specializes on All Cargo International route analysis, implementation and development. Our team provides professional guidance in obtaining worldwide both scheduled and charter authority.

Target Market(s)

Our target market are the airlines, logistics companies and commercial aviation related entities

Industry/Entity Type

Commercial Aviation

Coding

Coded - Design and coding required

Number of Pages Required

3 page

Requirements
Must have
• Illustrations of wide body freighters such V359, V342, V328

```html
<!DOCTYPE html>
<html lang="en">
<head>
<meta charset="utf-8">
<title>Calder Aviation</title>
<link href="https://fonts.googleapis.com/css2?family=Cinzel:wght@400;500;600&family=Roboto:wght@300;400;500;700&display=swap" rel="stylesheet">
<style>
:root{
  --navy:#0f1b4c;
  --navy-deep:#0a1238;
  --accent:#1e3f8f;
  --grey-bg:#eef0f3;
  --line:#c9ccd4;
  --text:#555a66;
  --heading:#1a1d2b;
  --white:#ffffff;
}
*{box-sizing:border-box;margin:0;padding:0}
html,body{width:1200px;height:4231px;overflow:hidden}
body{position:relative;font-family:'Roboto',sans-serif;color:var(--text);background:var(--white)}
section,header,footer{position:absolute;left:0;width:1200px}
.abs{position:absolute}
.serif{font-family:'Cinzel',serif}

/* nav */
.site-nav{top:0;height:72px;background:var(--navy-deep)}
.brand{position:absolute;left:120px;top:10px;width:160px;text-align:center;color:var(--white)}
.brand-name{font-family:'Cinzel',serif;font-size:25px;letter-spacing:1px;line-height:28px}
.brand-sub{font-size:10px;letter-spacing:9px;margin-top:2px;padding-left:9px}
.nav-links{position:absolute;top:28px;left:433px;display:flex;gap:0;font-size:13px;font-weight:700;color:var(--white)}
.nav-links span{margin-right:40px}

/* hero */
.hero{top:72px;height:570px}
.hero-photo{position:absolute;inset:0;background:linear-gradient(180deg,#5a6a83 0%,#a8806a 30%,#c48a52 42%,#4a3a3a 60%,#1c1f2c 100%)}
.hero-shade{position:absolute;inset:0;background:rgba(10,15,40,.25)}
.hero-title{position:absolute;top:280px;width:100%;text-align:center;font-family:'Cinzel',serif;font-size:54px;color:var(--white);letter-spacing:1px}
.hero-text{position:absolute;top:358px;left:290px;width:620px;text-align:center;color:var(--white);font-size:14px;line-height:24px}
.btn-start{position:absolute;top:424px;left:519px;width:161px;height:46px;background:var(--navy-deep);color:var(--white);font-size:13px;font-weight:700;display:flex;align-items:center;justify-content:center;gap:10px}
.slide-arrow{position:absolute;top:232px;width:34px;height:34px;border-radius:50%;background:var(--white);display:flex;align-items:center;justify-content:center}

/* labels */
.eyebrow{font-family:'Cinzel',serif;font-size:17px;color:var(--heading);letter-spacing:1px;display:flex;align-items:center;gap:8px}
.eyebrow::before{content:"";width:4px;height:16px;background:var(--navy)}
.eyebrow.after::before{display:none}
.eyebrow.after::after{content:"";width:4px;height:16px;background:var(--navy)}
.eyebrow.light{color:var(--white)}
.eyebrow.light::after{background:var(--white)}
.section-title{font-family:'Cinzel',serif;font-size:34px;color:var(--heading);text-align:center;width:100%}

/* about */
.about{top:642px;height:688px}
.about h2{position:absolute;left:112px;top:180px;font-family:'Cinzel',serif;font-weight:400;font-size:29px;line-height:38px;color:var(--heading)}
.about p{position:absolute;left:112px;top:268px;width:438px;font-size:13.4px;line-height:24.8px;text-align:justify}
.learn{position:absolute;left:112px;top:484px;font-size:12px;font-weight:700;color:var(--heading);display:flex;align-items:center;gap:8px}
.learn-ring{position:absolute;left:-2px;top:-9px;width:30px;height:30px;border:2px solid var(--heading);border-radius:50%;border-right-color:transparent}
.about-frame{position:absolute;left:639px;top:372px;width:561px;height:202px;border:4px solid var(--accent);border-right:none}
.about-photo{position:absolute;left:663px;top:138px;width:537px;height:413px;background:linear-gradient(135deg,#d9dde0,#9aa2a8 50%,#5a5450)}
.dots{position:absolute;background-image:radial-gradient(var(--navy) 1.4px,transparent 1.6px);background-size:8px 8px}

/* services */
.services{top:1330px;height:536px;background:var(--grey-bg)}
.service-card{position:absolute;top:216px;width:300px;height:235px;border:2px solid var(--line);text-align:center}
.service-card .icon{position:absolute;left:108px;top:-44px;width:84px;height:84px;border-radius:50%;background:var(--grey-bg);display:flex;align-items:center;justify-content:center}
.service-card .icon div{width:74px;height:74px;border-radius:50%;background:var(--navy-deep);border:3px solid var(--grey-bg);outline:2px solid var(--navy-deep);display:flex;align-items:center;justify-content:center}
.service-card h3{margin-top:68px;font-family:'Cinzel',serif;font-weight:500;font-size:16.5px;color:var(--heading)}
.service-card p{margin:28px auto 0;width:250px;font-size:13.4px;line-height:21.5px}
.service-card .go{position:absolute;left:140px;bottom:22px}

/* what we do */
.wwd{top:1866px;height:522px}
.wwd-bg{position:absolute;left:0;top:0;width:1200px;height:522px;background:linear-gradient(180deg,#1d2a61,#121d4e);border-radius:261px 0 0 261px}
.wwd-title{position:absolute;top:50px;width:100%;text-align:center;font-family:'Cinzel',serif;font-size:34px;color:var(--white)}
.wwd-card{position:absolute;top:156px;width:213px;height:245px;background:#e6e8ee;padding:18px}
.wwd-card .inner{width:100%;height:100%;border:2px solid var(--accent);background:var(--white);text-align:center;padding-top:12px}
.wwd-card .badge{width:62px;height:62px;margin:0 auto;border-radius:50%;background:#d6d9e0;display:flex;align-items:center;justify-content:center}
.wwd-card .badge div{width:48px;height:48px;border-radius:50%;background:var(--accent);display:flex;align-items:center;justify-content:center}
.wwd-card .badge.dark div{background:#3a3d46}
.wwd-card h4{margin-top:14px;font-size:12px;font-weight:700;color:var(--heading)}
.wwd-card .rule{width:36px;height:2px;background:var(--accent);margin:10px auto 0}
.wwd-card p{margin:12px auto 0;width:140px;font-size:11.5px;line-height:21px;color:#6a6e78}

/* blog */
.blog{top:2388px;height:854px}
.blog-main{position:absolute;left:126px;top:232px;width:470px;height:512px;background:var(--white);box-shadow:0 0 8px rgba(0,0,0,.12)}
.blog-main .photo{position:absolute;left:7px;top:7px;width:456px;height:243px;background:linear-gradient(180deg,#9aa6ae 0%,#c2c8cb 40%,#7d8a6a 72%,#5f6d4a 100%)}
.blog-main h3{position:absolute;left:25px;top:282px;width:420px;font-size:13px;font-weight:700;line-height:23px;color:var(--heading)}
.meta{position:absolute;left:25px;top:345px;display:flex;gap:34px;font-size:12px}
.meta span{display:flex;align-items:center;gap:6px}
.blog-main p{position:absolute;left:25px;top:390px;width:420px;font-size:13px;line-height:22px}
.read{position:absolute;left:25px;top:456px;font-size:12.5px;font-weight:700;color:var(--navy);text-decoration:underline;display:flex;align-items:center;gap:8px}
.blog-item{position:absolute;left:609px;width:492px;height:158px;background:var(--white);box-shadow:0 0 8px rgba(0,0,0,.12)}
.blog-item .photo{position:absolute;left:7px;top:7px;width:231px;height:144px}
.blog-item h4{position:absolute;left:264px;top:22px;width:200px;font-size:12.5px;font-weight:700;line-height:23px;color:var(--heading)}
.blog-item p{position:absolute;left:264px;top:78px;width:200px;font-size:13px;line-height:22px}

/* contact */
.contact{top:3242px;height:588px;background:var(--grey-bg)}
.contact-panel{position:absolute;left:148px;top:81px;width:361px;height:305px;background:var(--navy-deep)}
.contact-panel .eyebrow{position:absolute;right:107px;top:72px}
.contact-panel h2{position:absolute;right:107px;top:108px;text-align:right;font-family:'Cinzel',serif;font-weight:400;font-size:37px;line-height:47px;color:var(--white)}
.contact-frame{position:absolute;left:758px;top:81px;width:293px;height:303px;border:4px solid var(--navy-deep)}
.form{position:absolute;left:443px;top:117px;width:572px;height:389px;background:var(--white);box-shadow:0 0 10px rgba(0,0,0,.06)}
.form h3{position:absolute;left:42px;top:42px;font-family:'Cinzel',serif;font-weight:500;font-size:25px;color:var(--heading)}
.field{position:absolute;width:232px}
.field label{display:block;font-size:12.5px;font-weight:700;color:var(--heading)}
.field .val{margin-top:16px;font-size:11px;color:#777;padding-bottom:8px;border-bottom:1px solid var(--line)}
.send{position:absolute;left:482px;top:304px;width:48px;height:48px;border-radius:50%;background:var(--navy-deep);display:flex;align-items:center;justify-content:center}

/* footer */
.site-footer{top:3830px;height:401px;background:var(--navy-deep);color:var(--white)}
.site-footer .brand{top:100px;left:112px;width:190px}
.site-footer .brand-name{font-size:29px}
.socials{position:absolute;left:120px;top:172px;display:flex;gap:13px}
.socials span{width:36px;height:32px;border:1px solid var(--white);display:flex;align-items:center;justify-content:center}
.socials span i{width:8px;height:8px;background:var(--white);border-radius:50%}
.fcol{position:absolute;top:88px}
.fcol h5{font-size:16.5px;font-weight:700}
.fcol h5::after{content:"";display:block;width:30px;height:2px;background:var(--white);margin-top:10px}
.fcol ul{list-style:none;margin-top:14px}
.fcol li{font-size:13.5px;height:31px;display:flex;gap:10px;align-items:flex-start}
.fcol li b{font-weight:700;font-size:11px}
.fcontact li{height:auto;margin-bottom:14px;line-height:20px}
.frule{position:absolute;left:112px;top:320px;width:975px;height:1px;background:#4b5278}
.fbottom{position:absolute;top:352px;font-size:13px}
</style>
</head>
<body>

<header class="site-nav">
  <div class="brand"><div class="brand-name">CALDER</div><div class="brand-sub">AVIATION</div></div>
  <nav class="nav-links"><span>HOME</span><span>ABOUT US</span><span>OUR SERVICES</span><span>LATEST BLOG</span><span>REVIEWS</span><span>CONTACT US</span></nav>
</header>

<section class="hero">
  <div class="hero-photo" role="img" aria-label="Wide body jet on a runway at sunset"></div>
  <div class="hero-shade"></div>
  <div class="slide-arrow" style="left:37px"><svg width="12" height="12" viewBox="0 0 12 12"><path d="M8 1 3 6l5 5" stroke="#111" stroke-width="2" fill="none"/></svg></div>
  <div class="slide-arrow" style="left:1129px"><svg width="12" height="12" viewBox="0 0 12 12"><path d="m4 1 5 5-5 5" stroke="#111" stroke-width="2" fill="none"/></svg></div>
  <h1 class="hero-title">CALDER AVIATION</h1>
  <p class="hero-text">Calder team is a hands-on reliable alternative that works toward achieving your aircraft and aviation objectives by meeting your requirements and timeframe</p>
  <div class="btn-start">GET STARTED <svg width="14" height="14" viewBox="0 0 14 14"><circle cx="7" cy="7" r="7" fill="#fff"/><path d="M4 7h6M7.5 4.5 10 7l-2.5 2.5" stroke="#0a1238" stroke-width="1.8" fill="none"/></svg></div>
</section>

<section class="about">
  <div class="eyebrow abs" style="left:112px;top:146px">ABOUT US</div>
  <h2>WE ARE A CALDER<br>AVIATION'S MANAGEMENT</h2>
  <p>Founded in 2011, Calder Aviation's management has many years of experience in Aviation, a strong background in scheduled airlines with emphasis in all cargo operations, freight forwarding supply chain and freight logistics, as well as ACMI and CMI operations. Calder’s focuses in facilitating wet and dry lease operations, charter and ACMI programs consultancy, aircraft sales, leasing and procurement, aviation consultancy and aircraft management. Calder team is a hands-on reliable</p>
  <div class="learn"><span class="learn-ring"></span><span style="padding-left:24px">LEARN MORE ABOUT US</span><svg width="14" height="8" viewBox="0 0 14 8"><path d="M0 4h12M9 1l3 3-3 3" stroke="#1a1d2b" stroke-width="1.6" fill="none"/></svg></div>
  <div class="dots" style="left:612px;top:111px;width:120px;height:16px"></div>
  <div class="dots" style="left:612px;top:127px;width:48px;height:52px"></div>
  <div class="about-frame"></div>
  <div class="about-photo" role="img" aria-label="Management team reviewing documents in an office"></div>
</section>

<section class="services">
  <div class="eyebrow abs" style="left:526px;top:57px">WHAT WE DO</div>
  <h2 class="section-title abs" style="top:88px">OUR SERVICES</h2>

  <div class="service-card" style="left:112px">
    <div class="icon"><div><svg width="30" height="30" viewBox="0 0 30 30" fill="#fff"><path d="M15 3a10 10 0 0 1 10 10c0 4-4 7-6 9h-8c-2-2-6-5-6-9A10 10 0 0 1 15 3z"/><rect x="11" y="23" width="8" height="5"/></svg></div></div>
    <h3>AIRCRAFT FINANCE,</h3>
    <p>Sed ut perspiciatis unde omnis iste natus error sit voluptatem accusantium doloremque laudantium, totam rem</p>
    <svg class="go" width="16" height="16" viewBox="0 0 16 16"><circle cx="8" cy="8" r="8" fill="#0a1238"/><path d="M6 4.5 9.5 8 6 11.5" stroke="#fff" stroke-width="2" fill="none"/></svg>
  </div>
  <div class="service-card" style="left:450px">
    <div class="icon"><div><svg width="32" height="30" viewBox="0 0 32 30" fill="#fff"><circle cx="11" cy="10" r="4"/><circle cx="21" cy="10" r="4"/><path d="M4 22c1-5 13-5 14 0zM14 22c1-5 13-5 14 0z"/><path d="M3 6a13 13 0 0 1 6-4M29 24a13 13 0 0 1-6 4" stroke="#fff" stroke-width="2" fill="none"/></svg></div></div>
    <h3>TRADING</h3>
    <p>Sed ut perspiciatis unde omnis iste natus error sit voluptatem accusantium doloremque laudantium, totam rem</p>
    <svg class="go" width="16" height="16" viewBox="0 0 16 16"><circle cx="8" cy="8" r="8" fill="#0a1238"/><path d="M6 4.5 9.5 8 6 11.5" stroke="#fff" stroke-width="2" fill="none"/></svg>
  </div>
  <div class="service-card" style="left:788px">
    <div class="icon"><div><svg width="28" height="30" viewBox="0 0 28 30" fill="#fff"><rect x="3" y="3" width="16" height="24" rx="2"/><rect x="21" y="8" width="4" height="19"/><path d="M7 10h8M7 15h8M7 20h6" stroke="#0a1238" stroke-width="2"/></svg></div></div>
    <h3>PROCUREMENT &amp; LEASING</h3>
    <p>Sed ut perspiciatis unde omnis iste natus error sit voluptatem accusantium doloremque laudantium, totam rem</p>
    <svg class="go" width="16" height="16" viewBox="0 0 16 16"><circle cx="8" cy="8" r="8" fill="#0a1238"/><path d="M6 4.5 9.5 8 6 11.5" stroke="#fff" stroke-width="2" fill="none"/></svg>
  </div>
</section>

<section class="wwd">
  <div class="wwd-bg" role="img" aria-label="Dark blue tinted view of freighter aircraft in a hangar"></div>
  <h2 class="wwd-title">WHAT WE DO</h2>
  <div class="wwd-card" style="left:153px"><div class="inner">
    <div class="badge"><div><svg width="24" height="24" viewBox="0 0 24 24" fill="#fff"><path d="M2 12l5-5 5 3 5-3 5 5-5 5-5-3-5 3z"/></svg></div></div>
    <h4>SALE/LEASEBACK</h4><div class="rule"></div>
    <p>Sale-leaseback is a method of financing. If your company needs</p></div></div>
  <div class="wwd-card" style="left:381px"><div class="inner">
    <div class="badge dark"><div><svg width="24" height="24" viewBox="0 0 24 24" fill="#fff"><circle cx="12" cy="12" r="9"/><circle cx="12" cy="12" r="4" fill="#3a3d46"/></svg></div></div>
    <h4>FREIGHTER CONVERSION</h4><div class="rule"></div>
    <p>Pandemic has seen the resurgence of operators packing freight into the</p></div></div>
  <div class="wwd-card" style="left:607px"><div class="inner">
    <div class="badge"><div><svg width="24" height="24" viewBox="0 0 24 24" fill="#fff"><path d="M3 21 21 3M14 4l6 6-3 3-6-6zM4 14l6 6-3 1-4-4z" stroke="#fff" stroke-width="2"/></svg></div></div>
    <h4>WET LEASE</h4><div class="rule"></div>
    <p>Throughout our deep relationships within the industry, Calder</p></div></div>
  <div class="wwd-card" style="left:836px"><div class="inner">
    <div class="badge dark"><div><svg width="24" height="24" viewBox="0 0 24 24" fill="#fff"><rect x="5" y="3" width="12" height="18" rx="1"/><circle cx="17" cy="16" r="4"/><path d="M8 8h6M8 12h4" stroke="#3a3d46" stroke-width="2"/></svg></div></div>
    <h4>DRY LEASE</h4><div class="rule"></div>
    <p>We offer aircraft from our own portfolio on dry lease or could engage</p></div></div>
</section>

<section class="blog">
  <div class="eyebrow abs" style="left:535px;top:104px">RESOURCES</div>
  <h2 class="section-title abs" style="top:134px">LATEST BLOG</h2>

  <article class="blog-main">
    <div class="photo" role="img" aria-label="Wide body cargo freighter parked on an airfield"></div>
    <h3>SED UT PERSPICIATIS UNDE OMNIS ISTE NATUS ERROR SIT VOLUPTATEM ACCUSANTIUM</h3>
    <div class="meta">
      <span><svg width="11" height="11" viewBox="0 0 11 11"><rect x=".5" y="1.5" width="10" height="9" fill="none" stroke="#555" /><path d="M1 4h9" stroke="#555"/></svg>27/02/2020</span>
      <span><svg width="11" height="11" viewBox="0 0 11 11"><circle cx="5.5" cy="3.5" r="2.5" fill="none" stroke="#555"/><path d="M1 11c0-4 9-4 9 0" fill="none" stroke="#555"/></svg>Mara Linden</span>
      <span><svg width="12" height="11" viewBox="0 0 12 11"><path d="M1 1h10v6H5l-3 3V7H1z" fill="none" stroke="#555"/></svg>1,000</span>
    </div>
    <p>Natur aut odit aut fugit, sed quia consequuntur magni dolores eos qui ratione voluptatem sequi nesciunt.</p>
    <div class="read">READ MORE <svg width="13" height="13" viewBox="0 0 13 13"><circle cx="6.5" cy="6.5" r="5.5" fill="none" stroke="#0f1b4c" stroke-width="1.5"/><path d="M5 4l2.5 2.5L5 9" stroke="#0f1b4c" stroke-width="1.5" fill="none"/></svg></div>
  </article>

  <article class="blog-item" style="top:232px">
    <div class="photo" role="img" aria-label="Passenger jet climbing under a blue sky" style="background:linear-gradient(180deg,#7fa3cf,#c9d8e8 60%,#8a99a6)"></div>
    <h4>ET HARUM QUIDEM RERUM FACILIS EST ET</h4>
    <p>rnatur aut odit aut fugit, sed quia consequuntur.</p>
  </article>
  <article class="blog-item" style="top:409px">
    <div class="photo" role="img" aria-label="Colleagues meeting around a desk" style="background:linear-gradient(135deg,#c9b49c,#7e8a9a 60%,#3d3a3c)"></div>
    <h4>ET HARUM QUIDEM RERUM FACILIS EST ET</h4>
    <p>rnatur aut odit aut fugit, sed quia consequuntur.</p>
  </article>
  <article class="blog-item" style="top:587px">
    <div class="photo" role="img" aria-label="Team discussion in a bright office" style="background:linear-gradient(135deg,#d6d2cc,#8b8f96 60%,#3d3a3c)"></div>
    <h4>ET HARUM QUIDEM RERUM FACILIS EST ET</h4>
    <p>rnatur aut odit aut fugit, sed quia consequuntur.</p>
  </article>
</section>

<section class="contact">
  <div class="contact-frame"></div>
  <div class="contact-panel">
    <div class="eyebrow after light">CONTACT US</div>
    <h2>LET’S GO<br>GOOD<br>TOGETHER</h2>
  </div>
  <div class="dots" style="left:121px;top:343px;width:24px;height:52px"></div>
  <div class="dots" style="left:121px;top:395px;width:181px;height:17px"></div>
  <form class="form">
    <h3>Send Us a Message</h3>
    <div class="field" style="left:42px;top:102px"><label>YOUR NAME</label><div class="val">John Doe</div></div>
    <div class="field" style="left:296px;top:102px"><label>COMPANY</label><div class="val">johndoe@mailbox.net</div></div>
    <div class="field" style="left:42px;top:183px"><label>EMAIL ADDRESS</label><div class="val">johndoe@mailbox.net</div></div>
    <div class="field" style="left:296px;top:183px"><label>PHONE</label><div class="val">1 800 555 0142</div></div>
    <div class="field" style="left:42px;top:267px;width:440px"><label>MESSAGE</label><div class="val" style="padding-bottom:28px">Hi , do you have a moment to talk about Us</div></div>
    <div class="send"><svg width="20" height="20" viewBox="0 0 20 20"><path d="M2 10 18 2 13 18l-3-6z" fill="#fff"/></svg></div>
  </form>
</section>

<footer class="site-footer">
  <div class="brand"><div class="brand-name">CALDER</div><div class="brand-sub">AVIATION</div></div>
  <div class="socials"><span><i></i></span><span><i></i></span><span><i></i></span><span><i></i></span></div>
  <div class="fcol" style="left:397px"><h5>Quick Links</h5><ul><li><b>»</b>Home</li><li><b>»</b>About Us</li><li><b>»</b>Our Services</li><li><b>»</b>Latest Blog</li><li><b>»</b>COntact Us</li></ul></div>
  <div class="fcol" style="left:586px"><h5>Our Services</h5><ul><li><b>»</b>Aircraft Finance</li><li><b>»</b>Trading</li><li><b>»</b>Procurement</li><li><b>»</b>Leasing</li></ul></div>
  <div class="fcol fcontact" style="left:806px"><h5>Contact Us</h5><ul>
    <li><svg width="12" height="16" viewBox="0 0 12 16" style="flex:none;margin-top:3px"><path d="M6 0a6 6 0 0 1 6 6c0 4-6 10-6 10S0 10 0 6a6 6 0 0 1 6-6z" fill="#fff"/><circle cx="6" cy="6" r="2" fill="#0a1238"/></svg><span>Sed ut perspiciatis unde omnis iste<br>natus error sit voluptatem</span></li>
    <li><svg width="14" height="14" viewBox="0 0 14 14" style="flex:none;margin-top:3px"><path d="M3 1l3 3-2 2c1 2 2 3 4 4l2-2 3 3-2 2C6 13 1 8 1 3z" fill="#fff"/></svg>Tel No :&nbsp; 1 800 555 0142</li>
    <li><svg width="14" height="12" viewBox="0 0 14 12" style="flex:none;margin-top:4px"><rect width="14" height="11" fill="#fff"/><path d="M0 1l7 5 7-5" stroke="#0a1238" fill="none"/></svg>Email&nbsp; : &nbsp;info@calderaviation.com</li>
  </ul></div>
  <div class="frule"></div>
  <div class="fbottom" style="left:112px">© 2021 Calder Aviation. All Rights Reserved</div>
  <div class="fbottom" style="left:845px">Privacy Policy &nbsp; | &nbsp; Terms &amp; Conditions</div>
</footer>

</body>
</html>
```